Business Card Design

We are a commercial real estate brokerage in San Francisco, leasing office buildings downtown.
I would like a clean, elegant look. Simple but powerful .

Industry/Entity Type

Business

Contact Information for Business Card

Derek Holloway
lic# 07258143
415.555.0172
derek@velt-commercial.example
velt-commercial.example

```html
<!DOCTYPE html>
<html lang="en">
<head>
<meta charset="utf-8">
<title>VELT Commercial – Business Card</title>
<link href="https://fonts.googleapis.com/css2?family=Open+Sans:wght@400;600&display=swap" rel="stylesheet">
<style>
  :root {
    --backdrop: #3b332e;
    --card-black: #050505;
    --accent-slate: #8b9dc3;
    --text-white: #f2f2f2;
  }
  * { margin: 0; padding: 0; box-sizing: border-box; }
  html, body {
    width: 1200px; height: 844px; overflow: hidden;
    background: var(--backdrop);
    font-family: "Open Sans", Arial, sans-serif;
  }
  .canvas { position: relative; width: 1200px; height: 844px; }

  .card {
    position: absolute;
    width: 500px; height: 286px;
    background: var(--card-black);
    overflow: hidden;
    box-shadow: 0 10px 30px rgba(0,0,0,.45);
  }
  .card--contact { left: 60px; top: 279px; }
  .card--brand { left: 640px; top: 279px; }

  /* contact side */
  .band {
    position: absolute; left: 0; width: 100%; height: 12px;
    background: var(--accent-slate);
  }
  .band--top { top: 0; }
  .band--bottom { bottom: 0; }

  .skyline-art {
    position: absolute; left: 14px; bottom: 12px;
    width: 165px; height: 175px;
  }

  .contact-block {
    position: absolute; left: 196px; top: 46px; width: 280px;
    text-align: center; color: var(--text-white);
  }
  .contact-name {
    color: var(--accent-slate);
    font-weight: 600; font-size: 16px; letter-spacing: .5px;
    text-transform: uppercase;
  }
  .contact-license {
    margin-top: 24px; font-size: 15px;
  }
  .contact-license .label { color: var(--accent-slate); font-weight: 600; }
  .contact-lines {
    margin-top: 28px; font-size: 13.5px; line-height: 1.35;
  }

  /* brand side */
  .tab {
    position: absolute; width: 14px; height: 30px;
    background: var(--accent-slate);
  }
  .tab--left { left: 0; top: 176px; }
  .tab--right { right: 0; top: 30px; }

  .brand-mark {
    position: absolute; left: 50%; top: 50%;
    transform: translate(-50%, -50%);
    display: flex; align-items: center; gap: 14px;
  }
  .brand-square {
    width: 22px; height: 22px; background: var(--accent-slate);
  }
  .brand-name {
    color: var(--accent-slate);
    font-weight: 600; font-size: 30px; letter-spacing: 1px;
    text-transform: uppercase; white-space: nowrap;
  }
</style>
</head>
<body>
<main class="canvas">

  <section class="card card--contact">
    <div class="band band--top"></div>
    <svg class="skyline-art" role="img" aria-label="Illustration of downtown office towers" viewBox="0 0 165 175" preserveAspectRatio="none">
      <defs>
        <linearGradient id="skylineTone" x1="0" y1="0" x2="1" y2="1">
          <stop offset="0" stop-color="#a8a8a8"/>
          <stop offset="1" stop-color="#3c3c3c"/>
        </linearGradient>
      </defs>
      <rect x="0" y="0" width="165" height="175" fill="url(#skylineTone)"/>
    </svg>
    <div class="contact-block">
      <p class="contact-name">Derek Holloway</p>
      <p class="contact-license"><span class="label">LIC#</span> 07258143</p>
      <div class="contact-lines">
        <p>415.555.0172</p>
        <p>derek@velt-commercial.example</p>
        <p>velt-commercial.example</p>
      </div>
    </div>
    <div class="band band--bottom"></div>
  </section>

  <section class="card card--brand">
    <div class="tab tab--right"></div>
    <div class="brand-mark">
      <span class="brand-square"></span>
      <span class="brand-name">VELT Commercial</span>
    </div>
    <div class="tab tab--left"></div>
  </section>

</main>
</body>
</html>
```